Fenwick Ridge Accounting - New client package

I need a stationary package (presentation folder cover, welcome letter template/design, sample financial report template/design, business card and new logo) for my accounting business. I would like to see designs that use the color blue. Financial icons can be included in the design. The final design should be clean and communicate professionalism and the use of modern; user-friendly technology. Attached postcard files should help with overall design concept.

```html
<!DOCTYPE html>
<html lang="en">
<head>
<meta charset="utf-8">
<title>Fenwick Ridge Accounting – Presentation Folder</title>
<link rel="stylesheet" href="https://fonts.googleapis.com/css2?family=Montserrat:wght@400&family=Roboto:wght@400&display=swap">
<style>
  :root {
    --page-bg: #e4e4e6;
    --blue-deep: #0a5bd6;
    --blue-mid: #0799ea;
    --cyan-glow: #00c2f7;
    --navy: #002252;
    --navy-mid: #0a4a92;
    --white: #ffffff;
  }
  * { margin: 0; padding: 0; box-sizing: border-box; }
  html, body { width: 1200px; height: 854px; overflow: hidden; }
  body {
    background: radial-gradient(ellipse at 50% 40%, #f4f4f5 0%, var(--page-bg) 60%, #c9c9cc 100%);
    position: relative;
  }
  .folder-spread {
    position: absolute;
    left: 80px;
    top: 77px;
    width: 1040px;
    height: 700px;
    box-shadow: 0 12px 30px rgba(0, 0, 0, 0.25);
  }
  .folder-art { position: absolute; inset: 0; display: block; }

  .brand-name {
    position: absolute;
    font-family: "Montserrat", sans-serif;
    font-weight: 400;
    color: var(--white);
    text-transform: uppercase;
    line-height: 1.05;
  }
  .brand-name--front {
    left: 640px;
    top: 500px;
    font-size: 27px;
    letter-spacing: 2px;
  }
  .brand-name--back {
    left: 52px;
    top: 536px;
    font-size: 11px;
    letter-spacing: 1px;
  }
  .brand-mark {
    position: absolute;
    background: var(--white);
  }
  .brand-mark--front { left: 600px; top: 507px; width: 22px; height: 22px; }
  .brand-mark--back { left: 36px; top: 538px; width: 9px; height: 9px; }

  .contact-block {
    position: absolute;
    left: 36px;
    top: 598px;
    font-family: "Roboto", sans-serif;
    font-size: 9.5px;
    color: var(--white);
    line-height: 1.45;
  }
  .contact-block address { font-style: normal; margin-bottom: 6px; }
  .contact-list { list-style: none; }
  .contact-list li { display: flex; align-items: center; gap: 6px; }
  .contact-icon { width: 9px; height: 9px; flex: none; }
</style>
</head>
<body>
  <main class="folder-spread" aria-label="Presentation folder spread: back cover and front cover">
    <svg class="folder-art" viewBox="0 0 1040 700" xmlns="http://www.w3.org/2000/svg" aria-hidden="true">
      <defs>
        <radialGradient id="baseGlow" cx="0.34" cy="0.38" r="0.75">
          <stop offset="0" stop-color="var(--cyan-glow)"/>
          <stop offset="0.5" stop-color="var(--blue-mid)"/>
          <stop offset="1" stop-color="var(--blue-deep)"/>
        </radialGradient>
        <linearGradient id="frontNavy" x1="0" y1="0" x2="1" y2="1">
          <stop offset="0" stop-color="var(--navy-mid)"/>
          <stop offset="1" stop-color="var(--navy)"/>
        </linearGradient>
        <linearGradient id="backNavy" x1="0" y1="0" x2="0" y2="1">
          <stop offset="0" stop-color="#0a63c9"/>
          <stop offset="1" stop-color="var(--navy)"/>
        </linearGradient>
      </defs>

      <!-- base -->
      <rect class="base" width="1040" height="700" fill="url(#baseGlow)"/>

      <!-- back cover sweeps -->
      <path d="M0 700 C140 480 330 300 520 150 L520 700 Z" fill="#0a7fd6" opacity="0.35"/>
      <path d="M0 420 C90 520 230 570 380 580 C440 582 490 575 520 565 L520 700 L0 700 Z" fill="#004f9e" opacity="0.28"/>
      <path d="M40 700 C90 560 240 390 520 250" fill="none" stroke="#7fdcff" stroke-width="1" opacity="0.4"/>
      <path d="M250 700 C300 560 390 440 520 330" fill="none" stroke="#004b8c" stroke-width="1.5" opacity="0.5"/>
      <path d="M0 0 L520 0 L520 60 C360 80 200 60 0 40 Z" fill="#0a5fd8" opacity="0.35"/>
      <path d="M0 580 C120 610 260 660 460 700 L0 700 Z" fill="url(#backNavy)"/>

      <!-- front cover sweeps -->
      <path d="M520 180 C700 170 880 120 1040 60 L1040 0 L520 0 Z" fill="#0a5fd8" opacity="0.25"/>
      <path d="M540 300 C700 230 880 130 1040 40" fill="none" stroke="#8fe2ff" stroke-width="1.2" opacity="0.45"/>
      <path d="M520 300 C700 270 880 260 1040 270 L1040 700 L520 700 Z" fill="#0a6fcf" opacity="0.2"/>
      <path d="M520 470 C700 470 880 400 1040 270 L1040 700 L520 700 Z" fill="url(#frontNavy)"/>
      <path d="M520 620 C650 650 820 680 1040 690 L1040 700 L520 700 Z" fill="var(--blue-mid)" opacity="0.8"/>
      <path d="M520 600 C680 640 860 665 1040 672" fill="none" stroke="#2b86d4" stroke-width="1" opacity="0.6"/>

      <!-- fold -->
      <line x1="520" y1="0" x2="520" y2="700" stroke="#003f7a" stroke-width="1" opacity="0.35"/>
    </svg>

    <!-- back cover -->
    <span class="brand-mark brand-mark--back" aria-hidden="true"></span>
    <p class="brand-name brand-name--back">Fenwick Ridge Accounting</p>

    <div class="contact-block">
      <address>Level 12, Kestrel House<br>18 Larkin Street, Sydney</address>
      <ul class="contact-list">
        <li>
          <svg class="contact-icon" viewBox="0 0 10 10" aria-hidden="true"><path d="M2 1 L4 1 L4.6 3 L3.4 3.8 C4 5.2 4.8 6 6.2 6.6 L7 5.4 L9 6 L9 8 C9 8.6 8.6 9 8 9 C4.2 9 1 5.8 1 2 C1 1.4 1.4 1 2 1 Z" fill="var(--white)"/></svg>
          555-014-2237
        </li>
        <li>
          <svg class="contact-icon" viewBox="0 0 10 10" aria-hidden="true"><rect x="0.5" y="2" width="9" height="6" fill="var(--white)"/><path d="M0.5 2 L5 5.5 L9.5 2" fill="none" stroke="var(--navy)" stroke-width="0.8"/></svg>
          info@fenwickridgeaccounting.com
        </li>
        <li>
          <svg class="contact-icon" viewBox="0 0 10 10" aria-hidden="true"><g fill="none" stroke="var(--white)" stroke-width="0.8"><circle cx="5" cy="5" r="4.2"/><ellipse cx="5" cy="5" rx="1.8" ry="4.2"/><line x1="0.8" y1="5" x2="9.2" y2="5"/></g></svg>
          www.fenwickridgeaccounting.com
        </li>
      </ul>
    </div>

    <!-- front cover -->
    <span class="brand-mark brand-mark--front" aria-hidden="true"></span>
    <h1 class="brand-name brand-name--front">Fenwick<br>Ridge<br>Accounting</h1>
  </main>
</body>
</html>
```